Harborline Auto LLC

Car Dealer Customer Service
Address: 2874 Cresthaven Road, Shelbyville, TN 37162
web: www.harborlineautoxq.net
email: harborlineautoxq@mailnest.example
Phone: (931) 555-0148
Phone: (629) 555-0173

```html
<!DOCTYPE html>
<html lang="en">
<head>
<meta charset="utf-8">
<title>Harborline Auto — Business Card</title>
<link rel="stylesheet" href="https://fonts.googleapis.com/css2?family=Montserrat:wght@400;500;800&display=swap">
<style>
  :root {
    --backdrop: #333333;
    --brand-blue: #1e7bab;
    --icon-blue: #2a8fcb;
    --brand-gold: #eeb548;
    --card-white: #ffffff;
    --ink: #151515;
  }
  * { box-sizing: border-box; margin: 0; padding: 0; }
  html, body { width: 1200px; height: 984px; overflow: hidden; }
  body {
    background: var(--backdrop);
    font-family: "Montserrat", sans-serif;
    position: relative;
  }
  .card {
    position: absolute;
    left: 240px;
    width: 720px;
    height: 411px;
    box-shadow: 0 10px 30px rgba(0,0,0,0.45);
  }
  .card--front {
    top: 38px;
    background: var(--brand-blue);
    display: flex;
    flex-direction: column;
    align-items: center;
    justify-content: center;
    gap: 26px;
  }
  .front-mark {
    width: 150px;
    height: 150px;
    border-radius: 50%;
    background: var(--brand-gold);
  }
  .front-name {
    color: var(--card-white);
    font-weight: 800;
    font-size: 46px;
    letter-spacing: 2px;
    text-transform: uppercase;
  }
  .card--back {
    top: 520px;
    background: var(--card-white);
  }
  .contact {
    position: absolute;
    left: 42px;
    top: 46px;
    width: 400px;
  }
  .contact__name {
    color: var(--brand-blue);
    font-weight: 800;
    font-size: 28px;
    letter-spacing: 1px;
    text-transform: uppercase;
    margin-bottom: 14px;
  }
  .contact__address {
    font-size: 17px;
    line-height: 1.35;
    color: var(--ink);
    font-weight: 500;
    padding-left: 22px;
    margin-bottom: 16px;
  }
  .contact__list { list-style: none; }
  .contact__item {
    display: flex;
    align-items: center;
    gap: 12px;
    font-size: 17px;
    font-weight: 500;
    color: var(--ink);
    line-height: 1.6;
  }
  .contact__icon { width: 18px; height: 18px; flex: none; fill: var(--icon-blue); }
  .back-mark {
    position: absolute;
    right: 70px;
    top: 90px;
    width: 230px;
    height: 230px;
    border-radius: 50%;
    background: var(--icon-blue);
    display: flex;
    align-items: center;
    justify-content: center;
    text-align: center;
    color: var(--card-white);
    font-weight: 800;
    font-size: 24px;
    letter-spacing: 1px;
    line-height: 1.2;
    text-transform: uppercase;
  }
</style>
</head>
<body>
  <section class="card card--front">
    <div class="front-mark" aria-hidden="true"></div>
    <h1 class="front-name">Harborline Auto</h1>
  </section>

  <section class="card card--back">
    <div class="contact">
      <h2 class="contact__name">Harborline Auto</h2>
      <p class="contact__address">
        Car Dealer Customer Service<br>
        2874 Cresthaven Road<br>
        Shelbyville, TN 37162
      </p>
      <ul class="contact__list">
        <li class="contact__item">
          <svg class="contact__icon" viewBox="0 0 24 24" aria-hidden="true"><path d="M6.6 10.8a15.1 15.1 0 0 0 6.6 6.6l2.2-2.2c.3-.3.7-.4 1-.2 1.1.4 2.3.6 3.6.6.6 0 1 .4 1 1V20c0 .6-.4 1-1 1A17 17 0 0 1 3 4c0-.6.4-1 1-1h3.5c.6 0 1 .4 1 1 0 1.3.2 2.5.6 3.6.1.3 0 .7-.2 1z"/></svg>
          (931) 555-0148
        </li>
        <li class="contact__item">
          <svg class="contact__icon" viewBox="0 0 24 24" aria-hidden="true"><path d="M2 8c0-2 4-4 10-4s10 2 10 4v2h-5V8H7v2H2zM6 11h12l2 9H4z"/></svg>
          (629) 555-0173
        </li>
        <li class="contact__item">
          <svg class="contact__icon" viewBox="0 0 24 24" aria-hidden="true"><path d="M2 5h20v14H2zm2 2v.5l8 5.5 8-5.5V7z"/></svg>
          harborlineautoxq@mailnest.example
        </li>
        <li class="contact__item">
          <svg class="contact__icon" viewBox="0 0 24 24" aria-hidden="true"><circle cx="12" cy="12" r="10"/></svg>
          www.harborlineautoxq.net
        </li>
      </ul>
    </div>
    <div class="back-mark">Harborline<br>Auto</div>
  </section>
</body>
</html>
```